New Business Card Design Project

We require a business card design for Vexalund, a newly established Indian company.
Our focus is on the development, manufacturing, and export of a diverse array of pharmaceutical products on a global scale. The card should convey a professional appearance, as our primary markets are in Africa, China, and Southeast Asian nations.
We envision a two-sided business card, with the reverse side dedicated to a logo set against a solid color or an elegantly designed pattern. The corners should be rounded. We would appreciate seeing both horizontal and vertical design options. We trust the designer to utilize their expertise in creating this design.

The content for the business card is included in the attached Word file.

Target Market(s)

Our primary markets are in Africa, China, and Southeast Asian, Latin America, Maldives, Sri Lanka

Industry/Entity Type

Pharmaceutical Manufacturing and Export

Contact Information for Business Card

Colors

Designer to choose colors to be used in the design.

Requirements
Must have
• The reverse side of the business card features solely the logo along with the tagline, "Remedies of Life."
Should not have
• The logo should not exceed two instances, encompassing both the front and back sides of the card.

```html
<!DOCTYPE html>
<html lang="en">
<head>
<meta charset="utf-8">
<title>Vexalund – Business Card</title>
<link rel="stylesheet" href="https://fonts.googleapis.com/css2?family=Poppins:wght@400;600&display=swap">
<style>
  :root {
    --stage: #2b2b2b;
    --card-front: #1f1f1f;
    --card-back: #121212;
    --brand-blue: #29a3e0;
    --brand-coral: #f0604f;
    --ink-light: #f2f2f2;
    --ink-muted: #bdbdbd;
    --faint-blue: #1f2b33;
    --faint-coral: #322222;
  }
  * { box-sizing: border-box; margin: 0; padding: 0; }
  html, body { width: 1200px; height: 1200px; overflow: hidden; }
  body {
    background: var(--stage);
    font-family: "Poppins", sans-serif;
    display: flex;
    align-items: center;
    justify-content: center;
    gap: 60px;
  }
  .card {
    width: 440px;
    height: 680px;
    border-radius: 30px;
    position: relative;
    overflow: hidden;
    box-shadow: 0 18px 40px rgba(0,0,0,0.45);
  }
  .card--front {
    background: var(--card-front);
    display: flex;
    flex-direction: column;
    align-items: center;
  }
  .front__mark-area {
    margin-top: 50px;
    width: 260px;
    height: 260px;
    border-radius: 50%;
    background: radial-gradient(circle at 35% 45%, var(--faint-blue) 0%, transparent 60%),
                radial-gradient(circle at 68% 62%, var(--faint-coral) 0%, transparent 60%);
  }
  .front__details {
    margin-top: 30px;
    text-align: center;
    color: var(--ink-light);
    font-size: 16px;
    line-height: 1.4;
  }
  .front__name {
    color: var(--brand-blue);
    font-weight: 600;
    font-size: 30px;
    line-height: 1.2;
  }
  .front__divider {
    display: block;
    width: 14px;
    height: 2px;
    background: var(--brand-blue);
    margin: 12px auto;
  }
  .front__phone {
    color: var(--brand-coral);
    font-size: 24px;
    line-height: 1.3;
  }
  .card--back {
    background: var(--card-back);
    display: flex;
    flex-direction: column;
    align-items: center;
    justify-content: center;
  }
  .back__pattern {
    position: absolute;
    inset: 0;
    background: linear-gradient(215deg, rgba(255,255,255,0.28) 0%, rgba(255,255,255,0.10) 35%, rgba(0,0,0,0) 60%);
  }
  .back__brand {
    position: relative;
    display: flex;
    align-items: center;
    gap: 14px;
  }
  .back__dot {
    width: 26px;
    height: 26px;
    border-radius: 50%;
    background: var(--brand-coral);
  }
  .back__name {
    color: var(--brand-blue);
    font-weight: 600;
    font-size: 52px;
    letter-spacing: 1px;
  }
  .back__tagline {
    position: relative;
    margin-top: 10px;
    color: var(--ink-muted);
    font-size: 17px;
    letter-spacing: 3px;
  }
</style>
</head>
<body>
  <section class="card card--front">
    <div class="front__mark-area" role="img" aria-label="Large faint brand mark in muted blue and coral"></div>
    <div class="front__details">
      <p class="front__name">Arjun K. Solanki</p>
      <p class="front__role">CEO</p>
      <p class="front__company">Vexalund</p>
      <span class="front__divider"></span>
      <p>14, Nilgiri Lane, 440010</p>
      <p>Nagpur, India</p>
      <span class="front__divider"></span>
      <p class="front__phone">+919800012345</p>
      <p>asolanki@vexalund.com</p>
      <p>www.vexalund.com</p>
    </div>
  </section>

  <section class="card card--back">
    <div class="back__pattern" role="img" aria-label="Repeating glossy brand pattern on black"></div>
    <div class="back__brand">
      <span class="back__dot"></span>
      <span class="back__name">Vexalund</span>
    </div>
    <p class="back__tagline">Remedies of Life</p>
  </section>
</body>
</html>
```